ambitious event and festival agency from austria needs fresh business card design

A new design is due for the new headquarters and the new challenges. We organize events for different target groups from 16 to 60 years. The design should therefore be straightforward and not confused, so we are open to new colors and the logo may also be changed. In general, however, the most interesting suggestions are the most interesting ones. after this order we are looking for more graphics for lunquiva facebook instagramm homepage etc A new design is due for the new headquarters and the new challenges. We organize events for different target groups from 16 to 60 years. The design should therefore be straightforward and not confused, so we are open to new colors and the logo may also be changed. In general, however, the most interesting suggestions are the most interesting ones. after this order we are looking for more graphics for lunquiva facebook instagramm homepage etc A new design is due for the new headquarters and the new challenges. We organize events for different target groups from 16 to 60 years. The design should therefore be straightforward and not confused, so we are open to new colors and the logo may also be changed. In general, however, the most interesting suggestions are the most interesting ones. after this order we are looking for more graphics for lunquiva facebook instagramm homepage etc
Updates

Reason: I am sorry for this decision but i need some more time. No new designs please, there are so many good ones and I will have made a decision in the next 3 days.

Target Market(s)

Industry/Entity Type

Business

Font styles to use
Serif
Sans Serif

Colors

Designer to choose colors to be used in the design.

Requirements
Must have
Nice to have
Should not have

```html
<!DOCTYPE html>
<html lang="de">
<head>
<meta charset="utf-8">
<title>lunquiva – Visitenkarte</title>
<link href="https://fonts.googleapis.com/css2?family=Roboto:wght@400;500&family=Roboto+Condensed:wght@400;700&display=swap" rel="stylesheet">
<style>
  :root {
    --backdrop: #e3e3e3;
    --paper: #f4f4f4;
    --brand-red: #b02635;
    --slate: #5f6566;
    --band-grey: #6b7072;
    --ink: #3e4244;
    --rule: #7d8182;
    --white: #ffffff;
  }
  html, body {
    margin: 0;
    padding: 0;
    width: 1200px;
    height: 960px;
    overflow: hidden;
    background: var(--backdrop);
  }
  .canvas {
    position: relative;
    width: 1200px;
    height: 960px;
    font-family: "Roboto", Arial, sans-serif;
  }
  .card {
    position: absolute;
    height: 343px;
    box-shadow: 0 2px 4px rgba(0,0,0,0.25);
    overflow: hidden;
  }
  .card--front {
    left: 314px; top: 113px; width: 602px;
    background: var(--paper);
  }
  .card--back {
    left: 311px; top: 472px; width: 600px;
    background: var(--brand-red);
  }
  .wordmark {
    position: absolute;
    font-family: "Roboto", Arial, sans-serif;
    font-weight: 500;
    line-height: 1;
    letter-spacing: 0.5px;
    margin: 0;
  }
  .card--front .wordmark { right: 41px; top: 40px; font-size: 52px; color: var(--brand-red); }
  .card--back .wordmark { right: 43px; top: 234px; font-size: 46px; color: var(--white); }

  .holder { position: absolute; left: 38px; top: 186px; }
  .holder__name {
    margin: 0;
    font-family: "Roboto Condensed", Arial, sans-serif;
    font-weight: 700;
    font-size: 21px;
    color: var(--brand-red);
    letter-spacing: 0.2px;
  }
  .holder__role {
    margin: 3px 0 0;
    font-family: "Roboto Condensed", Arial, sans-serif;
    font-size: 15.5px;
    color: var(--slate);
    letter-spacing: 0.4px;
  }
  .divider {
    position: absolute; left: 38px; top: 240px;
    width: 523px; height: 1px; background: var(--rule);
  }
  .contact {
    position: absolute; left: 38px; top: 254px;
    margin: 0; padding: 0; list-style: none;
    font-size: 14px; color: var(--ink);
  }
  .contact li { display: flex; align-items: center; height: 20px; }
  .contact svg { width: 13px; height: 13px; margin-right: 8px; fill: var(--brand-red); }
  .address {
    position: absolute; right: 40px; top: 256px;
    margin: 0; text-align: right; font-style: normal;
    font-size: 14px; line-height: 19px; color: var(--ink);
  }
  .footer-band { position: absolute; left: 0; bottom: 0; width: 602px; height: 33px; }
  .web {
    position: absolute; right: 32px; bottom: 9px;
    font-size: 13px; letter-spacing: 4.4px; color: var(--white);
  }
  .card--back .web { right: 38px; bottom: 40px; font-size: 13px; letter-spacing: 7.6px; }
</style>
</head>
<body>
<main class="canvas">
  <section class="card card--front" aria-label="Vorderseite">
    <p class="wordmark">lunquiva</p>

    <div class="holder">
      <h1 class="holder__name">MARKUS FELDHOFER</h1>
      <p class="holder__role">GESCHAFTSFUHRER</p>
    </div>
    <div class="divider"></div>

    <ul class="contact">
      <li>
        <svg viewBox="0 0 24 24" aria-hidden="true"><path d="M6.6 10.8a15.1 15.1 0 0 0 6.6 6.6l2.2-2.2c.3-.3.7-.4 1-.2 1.1.4 2.3.6 3.6.6.6 0 1 .4 1 1V20c0 .6-.4 1-1 1A17 17 0 0 1 3 4c0-.6.4-1 1-1h3.5c.6 0 1 .4 1 1 0 1.3.2 2.5.6 3.6.1.3 0 .7-.2 1z"/></svg>
        +43 650 418 273 5
      </li>
      <li>
        <svg viewBox="0 0 24 24" aria-hidden="true"><path d="M2 5h20v2l-10 6L2 7z"/><path d="M2 9l10 6 10-6v10H2z"/></svg>
        m.feldhofer@lunquiva.eu
      </li>
    </ul>

    <address class="address">Birkenweg 12<br>A4820 talheim</address>

    <svg class="footer-band" viewBox="0 0 602 33" aria-hidden="true">
      <polygon points="0,11 343,11 336,21 0,21" fill="var(--band-grey)"/>
      <polygon points="0,21 336,21 356,0 602,0 602,33 0,33" fill="var(--brand-red)"/>
    </svg>
    <span class="web">www.lunquiva.eu</span>
  </section>

  <section class="card card--back" aria-label="Rückseite">
    <p class="wordmark">lunquiva</p>
    <span class="web">www.lunquiva.eu</span>
  </section>
</main>
</body>
</html>
```